Business Card Design & Gift cards, Gift Cert, Donation Card

Retail Gift Store-in addition to Business Cards we'd like sequenced 2 sided Gift cards, Gift Certificate Cards, and Donation Cards.please see examples and email for clarificationlogos attached with examples-
Gift Card, Gift Certificate and Donation Card will all be same style just differant upper right title, with back side info as example.
business card, as example is single sided.
looking for additional ideas for layout

Industry/Entity Type

Business

Contact Information for Business Card

211 Newman St.East Tawas, MI 48730989.362.8730Office@BrewKrew.com

Requirements
Must have
• Blue as per example
• Logos provided
• like gradiant background

```html
<!DOCTYPE html>
<html lang="en">
<head>
<meta charset="utf-8">
<title>Tillow Marsh – Business Card &amp; Gift Card</title>
<link rel="stylesheet" href="https://fonts.googleapis.com/css2?family=Comic+Neue:wght@400;700&display=swap">
<style>
  :root {
    --page-bg: #e9e9ea;
    --card-bg: #ffffff;
    --ink: #111111;
    --ink-soft: #555555;
    --rule: #cfcfcf;
    --band-dark: #151515;
    --band-grey: #9a9a9a;
    --brand-blue: #2f3fb8;
    --faint-blue: #e6e9f8;
    --faint-sun: #fbf4d2;
  }
  * { box-sizing: border-box; margin: 0; padding: 0; }
  html, body { width: 1105px; height: 1200px; overflow: hidden; }
  body {
    background: var(--page-bg);
    font-family: "Comic Neue", "Comic Sans MS", cursive;
    color: var(--ink);
    position: relative;
  }
  .card {
    position: absolute;
    left: 196px;
    width: 720px;
    height: 412px;
    background: var(--card-bg);
    border-radius: 25px;
    overflow: hidden;
  }
  .card--front { top: 146px; }
  .card--back { top: 602px; }

  /* Front */
  .brand-name {
    position: absolute;
    left: 40px; top: 166px;
    width: 280px;
    text-align: center;
    font-size: 33px;
    font-weight: 400;
    letter-spacing: 0;
    color: var(--ink);
    line-height: 1;
    white-space: nowrap;
  }
  .divider {
    position: absolute;
    left: 337px; top: 70px;
    width: 1px; height: 232px;
    background: var(--rule);
  }
  .contact {
    position: absolute;
    left: 373px; top: 74px;
    font-size: 22px;
    line-height: 1;
    color: var(--ink-soft);
    font-weight: 400;
  }
  .contact p { height: 25px; white-space: nowrap; }
  .contact .gap { margin-top: 11px; }
  .contact .icon { display: inline-block; width: 16px; height: 16px; margin-right: 8px; vertical-align: -1px; }
  .band {
    position: absolute;
    left: 0; top: 363px;
    width: 100%; height: 31px;
    background: linear-gradient(90deg, var(--band-dark) 0%, var(--band-dark) 76%, var(--band-grey) 76%, #bcbcbc 100%);
  }
  .web {
    position: absolute;
    left: 0; width: 538px; top: 0;
    text-align: center;
    color: #ffffff;
    font-size: 19px;
    font-weight: 700;
    letter-spacing: 3px;
    line-height: 31px;
  }
  .brand-dot {
    position: absolute;
    left: 563px; top: 346px;
    width: 44px; height: 44px;
    border-radius: 50%;
    background: var(--brand-blue);
  }

  /* Back */
  .card-number {
    position: absolute;
    right: 40px; top: 40px;
    font-size: 18px;
    font-weight: 400;
    line-height: 1;
  }
  .faint-art {
    position: absolute;
    left: 232px; top: 33px;
    width: 325px; height: 352px;
    border-radius: 40px;
    background: linear-gradient(180deg, var(--faint-blue) 0%, #eef0fa 65%, var(--faint-sun) 100%);
    opacity: 0.8;
  }
  .field {
    position: absolute;
    left: 58px;
    right: 40px;
    display: flex;
    align-items: flex-end;
    line-height: 1;
  }
  .field .label { white-space: nowrap; }
  .field .line { flex: 1; border-bottom: 1.5px solid #333; margin-left: 14px; margin-bottom: 4px; }
  .field--large { font-size: 27px; right: 53px; }
  .field--large .label { font-weight: 700; }
  .field--small { font-size: 22px; }
  .field--small .label { font-weight: 400; }
  .f-to { top: 80px; }
  .f-form { top: 137px; }
  .f-issued { top: 224px; }
  .f-expire { top: 272px; }
  .f-employee { top: 321px; }
  .f-employee .line { margin-left: 24px; }
</style>
</head>
<body>

<section class="card card--front" aria-label="Business card">
  <div class="brand-name">TILLOW MARSH</div>
  <div class="divider"></div>
  <div class="contact">
    <p>482 Larkfield Ave.</p>
    <p>Harlow Bay, MI 48815</p>
    <p class="gap">
      <svg class="icon" viewBox="0 0 16 16" aria-hidden="true"><path fill="#333" d="M3.5 1.5l2.6 0.4 1 3.2-1.7 1.2a8 8 0 0 0 4.3 4.3l1.2-1.7 3.2 1 0.4 2.6c-0.3 1-1.3 1.6-2.4 1.5C6.6 13.4 2.6 9.4 2 4 1.9 2.9 2.5 1.8 3.5 1.5z"/></svg>989.517.4296
    </p>
    <p>
      <svg class="icon" viewBox="0 0 16 16" aria-hidden="true"><rect x="1" y="3.5" width="14" height="9.5" fill="#333"/><path d="M1.5 4l6.5 5 6.5-5" fill="none" stroke="#fff" stroke-width="1.3"/></svg>Office@TillowMarsh.com
    </p>
    <p class="gap">Gourmet Food</p>
    <p>Fine Wines | Gift Baskets</p>
    <p>Kitchen &amp; Bath Accessories</p>
    <p>Candles | Cards | Soaps</p>
  </div>
  <div class="band">
    <div class="web">www.TillowMarsh.com</div>
  </div>
  <div class="brand-dot" aria-hidden="true"></div>
</section>

<section class="card card--back" aria-label="Gift card back">
  <div class="faint-art" role="img" aria-label="Faint brand illustration watermark in pale blue and yellow"></div>
  <div class="card-number">Card Number : 58724</div>
  <div class="field field--large f-to"><span class="label">To :</span><span class="line"></span></div>
  <div class="field field--large f-form"><span class="label">Form :</span><span class="line"></span></div>
  <div class="field field--small f-issued"><span class="label">Date&nbsp; Issued :</span><span class="line"></span></div>
  <div class="field field--small f-expire"><span class="label">Expiration Date :</span><span class="line"></span></div>
  <div class="field field--small f-employee"><span class="label">Employee :</span><span class="line"></span></div>
</section>

</body>
</html>
```